VIP Card Design Project

uZorvo is a premium sneaker store selling brand name sneakers like Volta, Rexa, Kembro and etc. ( www.uzorvoshop.com ) We need to design a VIP card to promote one of our discount program called "Uzorvo VIP Band 17", which offers 24% discount off all full-priced items. The idea is because we have a "Peakline Gym center" (peaklinegym.com) next door and we are trying to design a discount program for people going to the fitness center.
The design is for the front of the card. The back will be black and white with benefits information and member information.
The front design need to include our logo, "VIP", "Band 17" and our web address "Uzorvo.com" and Chatterly and quibbr logo.
It will be a plastic card in the size of 3.375x2.125 (bleed size 3.5x2.25)

```html
<!DOCTYPE html>
<html lang="en">
<head>
<meta charset="utf-8">
<title>Uzorvo VIP Band 17 Card</title>
<link rel="stylesheet" href="https://fonts.googleapis.com/css2?family=Bree+Serif&family=PT+Sans:wght@400;700&display=swap">
<style>
  :root {
    --stage: #ece8e3;
    --card-black: #1d1b1b;
    --brand-green: #3fae3a;
    --brand-red: #e2262b;
    --brand-orange: #ec6f2a;
    --brand-amber: #f7b447;
    --ink-grey: #4a4a4a;
    --paper: #ffffff;
    --tile-red: #c9553f;
    --tile-dark: #5a5648;
    --tile-blue: #6d8fa6;
  }
  * { box-sizing: border-box; margin: 0; padding: 0; }
  html, body { width: 1200px; height: 435px; overflow: hidden; }
  body { background: var(--stage); position: relative; }

  .card {
    position: absolute;
    top: 60px;
    width: 510px;
    height: 317px;
    overflow: hidden;
    box-shadow: 3px 4px 8px rgba(0,0,0,0.35);
  }

  /* Front */
  .card-front { left: 55px; background: var(--card-black); }
  .product-tile {
    position: absolute;
    top: 17px;
    width: 148px;
    height: 71px;
    border-radius: 9px;
    overflow: hidden;
  }
  .product-tile .photo { position: absolute; inset: 0; }
  .tile-1 { left: 17px; }
  .tile-2 { left: 178px; }
  .tile-3 { left: 340px; }
  .tile-1 .photo { background: linear-gradient(180deg, #a9a79b 0%, var(--tile-red) 55%, #d9d5cc 100%); }
  .tile-2 .photo { background: linear-gradient(180deg, #8d8a7a 0%, var(--tile-dark) 55%, #b9cf3a 100%); }
  .tile-3 .photo { background: linear-gradient(180deg, #9b9a8a 0%, var(--tile-blue) 55%, #d8d4c8 100%); }
  .discount-badge {
    position: absolute;
    left: 2px;
    top: 33px;
    width: 66px;
    height: 38px;
  }
  .discount-badge svg { position: absolute; inset: 0; }
  .discount-badge span {
    position: absolute;
    inset: 0;
    display: flex;
    align-items: center;
    justify-content: center;
    font-family: "Bree Serif", serif;
    font-size: 18px;
    color: var(--brand-red);
  }
  .tagline {
    position: absolute;
    top: 124px;
    left: 0; right: 0;
    text-align: center;
    font-family: "Bree Serif", serif;
    font-size: 22px;
    color: var(--brand-green);
  }
  .program-name {
    position: absolute;
    top: 162px;
    left: 0; right: 0;
    text-align: center;
    font-family: "Bree Serif", serif;
    font-size: 27px;
    color: var(--brand-red);
  }
  .brand-name {
    position: absolute;
    top: 196px;
    left: 118px;
    font-family: "Bree Serif", serif;
    font-size: 46px;
    line-height: 1;
    color: var(--brand-green);
  }
  .social-list {
    position: absolute;
    top: 212px;
    left: 312px;
    display: flex;
    flex-direction: column;
    gap: 4px;
    list-style: none;
  }
  .social-list li {
    display: flex;
    align-items: center;
    gap: 4px;
    font-family: "Bree Serif", serif;
    font-size: 11px;
    color: #ffffff;
  }
  .social-list li::before {
    content: "";
    width: 11px;
    height: 11px;
    background: #3b6fb6;
  }
  .front-swoosh { position: absolute; left: 0; bottom: 0; width: 510px; height: 317px; }
  .web-address {
    position: absolute;
    top: 266px;
    left: 0; right: 0;
    text-align: center;
    font-family: "Bree Serif", serif;
    font-size: 15px;
    letter-spacing: 1px;
    color: var(--brand-red);
  }

  /* Back */
  .card-back {
    left: 645px;
    width: 505px;
    background: var(--paper);
    padding: 31px 38px 0 38px;
    font-family: "PT Sans", sans-serif;
  }
  .member-line {
    font-size: 10.5px;
    color: var(--brand-red);
    white-space: nowrap;
  }
  .member-line .blank { letter-spacing: -0.5px; }
  .benefits-title {
    margin-top: 9px;
    font-size: 17px;
    font-weight: 700;
    color: var(--brand-red);
  }
  .benefits-intro {
    margin-top: 9px;
    font-size: 11.5px;
    color: var(--ink-grey);
  }
  .benefit-list {
    margin-top: 8px;
    list-style: none;
    font-size: 11.5px;
    line-height: 1.4;
    color: var(--ink-grey);
  }
  .benefit-list li {
    display: flex;
    gap: 5px;
    margin-bottom: 5px;
  }
  .benefit-list .marker { color: var(--brand-red); width: 9px; flex: none; }
</style>
</head>
<body>

<section class="card card-front" aria-label="VIP card front">
  <div class="product-tile tile-1">
    <div class="photo" role="img" aria-label="Photo of a red running sneaker"></div>
    <div class="discount-badge">
      <svg viewBox="0 0 66 38" aria-hidden="true"><polygon fill="#fff" points="33,0 38,6 46,2 48,9 57,8 55,15 64,18 57,22 62,29 53,30 53,37 45,34 40,38 33,33 26,38 21,34 13,37 13,30 4,29 9,22 2,18 11,15 9,8 18,9 20,2 28,6"/></svg>
      <span>24%</span>
    </div>
  </div>
  <div class="product-tile tile-2">
    <div class="photo" role="img" aria-label="Photo of a black sneaker with a neon yellow sole"></div>
    <div class="discount-badge">
      <svg viewBox="0 0 66 38" aria-hidden="true"><polygon fill="#fff" points="33,0 38,6 46,2 48,9 57,8 55,15 64,18 57,22 62,29 53,30 53,37 45,34 40,38 33,33 26,38 21,34 13,37 13,30 4,29 9,22 2,18 11,15 9,8 18,9 20,2 28,6"/></svg>
      <span>24%</span>
    </div>
  </div>
  <div class="product-tile tile-3">
    <div class="photo" role="img" aria-label="Photo of a blue running sneaker"></div>
    <div class="discount-badge">
      <svg viewBox="0 0 66 38" aria-hidden="true"><polygon fill="#fff" points="33,0 38,6 46,2 48,9 57,8 55,15 64,18 57,22 62,29 53,30 53,37 45,34 40,38 33,33 26,38 21,34 13,37 13,30 4,29 9,22 2,18 11,15 9,8 18,9 20,2 28,6"/></svg>
      <span>24%</span>
    </div>
  </div>

  <p class="tagline">discount off all full-priced items.</p>
  <h1 class="program-name">Uzorvo VIP Band 17</h1>

  <svg class="front-swoosh" viewBox="0 0 510 317" aria-hidden="true">
    <defs>
      <linearGradient id="swoosh-fill" x1="0" y1="0" x2="1" y2="0">
        <stop offset="0" stop-color="#ea6a2a"/>
        <stop offset="0.5" stop-color="#f4a53f"/>
        <stop offset="1" stop-color="#e9662a"/>
      </linearGradient>
    </defs>
    <path d="M0,232 C150,268 330,262 510,206 L510,317 L0,317 Z" fill="url(#swoosh-fill)"/>
    <path d="M150,300 C300,282 420,258 510,214 L510,222 C420,266 300,292 150,300 Z" fill="var(--brand-green)"/>
    <path d="M0,232 C150,268 330,262 510,206" fill="none" stroke="var(--card-black)" stroke-width="2"/>
  </svg>

  <div class="brand-name">uZorvo</div>
  <ul class="social-list">
    <li>Chatterly</li>
    <li>quibbr</li>
  </ul>
  <p class="web-address">www.Uzorvo.com</p>
</section>

<section class="card card-back" aria-label="VIP card back">
  <p class="member-line">Member Name :<span class="blank">...........................................................</span>Member ID :<span class="blank">.............................................................</span></p>
  <h2 class="benefits-title">Benefits :-</h2>
  <p class="benefits-intro">The UZORVO Member Program entitles Members to the following benefits:</p>
  <ol class="benefit-list">
    <li><span class="marker">a.</span><span>20% OFF your entire first purchase after you sign up (Limited Time Offer).<br>Certain items are excluded from this offer. Please see stores for details.</span></li>
    <li><span class="marker">b.</span><span>10% OFF every purchase while being a member.<br>Certain items are excluded from this offer. Please see stores for details.</span></li>
    <li><span class="marker">c.</span><span>Additional 10% OFF and FREE SHIPPING when an item is out of stock<br>in store but can be shipped to you from another location.</span></li>
    <li><span class="marker">d.</span><span>Eligible to purchase exclusive items offered to members only.<br>Purchasing of exclusive items is limited to 1 item per member per 30 days.<br>Please see stores for details.</span></li>
  </ol>
</section>

</body>
</html>
```